Business Card for brovaLINK

Create a Business Card with an existing logo for brovaLINK AG. We are a Information Technology company that does consulting and developing SW to automate business processes. The main colors are given from the logo.

Industry/Entity Type

Business

Requirements
Nice to have
• we use a a font style Century Gothic in our documents

```html
<!DOCTYPE html>
<html lang="en">
<head>
<meta charset="utf-8">
<title>brovaLINK AG – Business Card</title>
<link href="https://fonts.googleapis.com/css2?family=Questrial&family=Roboto+Condensed:wght@400;700&display=swap" rel="stylesheet">
<style>
  :root {
    --page-bg: #e9e6e1;
    --card-top: #2b2b2d;
    --card-bottom: #0c0c0d;
    --brand-white: #f4f4f4;
    --brand-blue: #2b9ad9;
    --brand-green: #8cc63f;
    --text-light: #e6e6e6;
    --accent-glow: rgba(255,255,255,0.06);
  }
  * { box-sizing: border-box; margin: 0; padding: 0; }
  html, body { width: 1200px; height: 913px; overflow: hidden; }
  body {
    background: var(--page-bg);
    display: flex;
    align-items: center;
    justify-content: center;
    gap: 40px;
  }
  .card {
    position: relative;
    width: 540px;
    height: 309px;
    border-radius: 4px;
    overflow: hidden;
    background: linear-gradient(160deg, var(--card-top) 0%, #1a1a1c 45%, var(--card-bottom) 100%);
    box-shadow: 0 10px 30px rgba(0,0,0,0.25);
  }
  .card__decor {
    position: absolute;
    right: -70px;
    top: -90px;
    width: 300px;
    height: 300px;
    border-radius: 50%;
    background: var(--accent-glow);
  }
  .brand {
    position: absolute;
    display: flex;
    align-items: center;
    gap: 14px;
  }
  .brand__dot {
    width: 44px;
    height: 44px;
    border-radius: 50%;
    background: var(--brand-blue);
  }
  .brand__name {
    font-family: "Questrial", "Century Gothic", sans-serif;
    font-size: 46px;
    color: var(--brand-white);
    letter-spacing: 0.5px;
  }
  .card--front .brand { left: 50%; top: 50%; transform: translate(-50%, -50%); }
  .card--back .brand { left: 34px; top: 170px; }
  .card--back .brand__dot { width: 34px; height: 34px; }
  .card--back .brand__name { font-size: 36px; }

  .contact {
    position: absolute;
    left: 300px;
    top: 54px;
    font-family: "Roboto Condensed", "Arial Narrow", sans-serif;
  }
  .contact__name {
    font-weight: 700;
    font-size: 17px;
    color: var(--brand-blue);
  }
  .contact__role {
    font-size: 12px;
    color: var(--brand-green);
    margin-bottom: 22px;
  }
  .contact__list { list-style: none; }
  .contact__item {
    display: flex;
    align-items: center;
    gap: 10px;
    font-size: 12.5px;
    color: var(--text-light);
    line-height: 20px;
  }
  .contact__icon { width: 12px; height: 12px; flex: none; }
</style>
</head>
<body>
  <section class="card card--front" aria-label="Card front">
    <div class="card__decor"></div>
    <div class="brand">
      <span class="brand__dot"></span>
      <span class="brand__name">brovaLINK</span>
    </div>
  </section>

  <section class="card card--back" aria-label="Card back">
    <div class="card__decor"></div>
    <div class="brand">
      <span class="brand__dot"></span>
      <span class="brand__name">brovaLINK</span>
    </div>
    <div class="contact">
      <p class="contact__name">Lukas Brenner</p>
      <p class="contact__role">CEO</p>
      <ul class="contact__list">
        <li class="contact__item">
          <svg class="contact__icon" viewBox="0 0 12 12"><path d="M6 0.5a4 4 0 0 0-4 4c0 3 4 7 4 7s4-4 4-7a4 4 0 0 0-4-4z" fill="var(--brand-blue)"/><circle cx="6" cy="4.5" r="1.4" fill="#111"/></svg>
          Lindenweg 8, 5000 Aarau, Switzerland
        </li>
        <li class="contact__item">
          <svg class="contact__icon" viewBox="0 0 12 12"><path d="M1 4c0-2 2-3 5-3s5 1 5 3l-2 1-1-1.5H4L3 5zM2.5 6h7l1 5h-9z" fill="var(--brand-blue)"/></svg>
          +41 56 000 12 34
        </li>
        <li class="contact__item">
          <svg class="contact__icon" viewBox="0 0 12 12"><rect x="3" y="0.5" width="6" height="11" rx="1" fill="var(--brand-blue)"/><rect x="4" y="2" width="4" height="6" fill="#111"/></svg>
          +41 79 000 56 78
        </li>
        <li class="contact__item">
          <svg class="contact__icon" viewBox="0 0 12 12"><rect x="0.5" y="2.5" width="11" height="7" fill="var(--brand-blue)"/><path d="M0.5 2.5 6 7l5.5-4.5" fill="none" stroke="#111" stroke-width="1"/></svg>
          lukas.brenner@brovalink.ch
        </li>
        <li class="contact__item">
          <svg class="contact__icon" viewBox="0 0 12 12"><circle cx="6" cy="6" r="5.5" fill="var(--brand-blue)"/><path d="M0.5 6h11M6 0.5c-3 3-3 8 0 11M6 0.5c3 3 3 8 0 11" fill="none" stroke="#111" stroke-width="0.8"/></svg>
          www.brovalink.ch
        </li>
      </ul>
    </div>
  </section>
</body>
</html>
```